Velora Entertainment

Logo for business card design

Target Market(s)

potential film investors and screenwriters

Industry/Entity Type

Business

Contact Information for Business Card

as shown, website here is a placeholder position

Requirements
Must have
• great visual appeal
Nice to have
• harmony of colors; must evoke spirit of
• U.S.-China cooperation

```html
<!DOCTYPE html>
<html lang="en">
<head>
<meta charset="utf-8">
<title>Velora Entertainment — Business Card</title>
<link rel="stylesheet" href="https://fonts.googleapis.com/css2?family=Source+Sans+3:wght@400;600;700&display=swap">
<style>
  :root {
    --backdrop: #9a9b9c;
    --card-front: #f1f2f4;
    --card-back: #838487;
    --ink: #1d1d1f;
    --accent-red: #c8101c;
    --accent-yellow: #dcbd00;
    --accent-navy: #131777;
    --light-type: #e3e8ec;
  }
  html, body {
    margin: 0;
    padding: 0;
    overflow: hidden;
  }
  body {
    width: 1105px;
    height: 1200px;
    background: var(--backdrop);
    font-family: "Source Sans 3", "Myriad Pro", Arial, sans-serif;
    position: relative;
  }
  .card {
    position: absolute;
    left: 178px;
    width: 748px;
    height: 428px;
    box-shadow: 0 10px 22px rgba(0, 0, 0, 0.28);
  }
  .card--front {
    top: 118px;
    background: var(--card-front);
  }
  .card--back {
    top: 636px;
    background: var(--card-back);
  }

  .contact {
    position: absolute;
    left: 48px;
    top: 40px;
    color: var(--ink);
    font-size: 20px;
    line-height: 28px;
  }
  .contact__name {
    margin: 0;
    color: var(--accent-red);
    font-size: 26px;
    font-weight: 600;
    line-height: 34px;
  }
  .contact__role {
    margin: 0 0 26px;
  }
  .contact__address {
    margin: 0 0 14px;
    font-style: normal;
  }
  .contact__lines {
    margin: 0;
    padding: 0;
    list-style: none;
  }
  .contact__label {
    color: var(--accent-red);
    font-weight: 700;
  }

  .brand {
    position: absolute;
    display: flex;
    align-items: center;
    gap: 14px;
    font-weight: 700;
    line-height: 1.05;
  }
  .brand__mark {
    width: 40px;
    height: 40px;
    background: var(--accent-red);
    flex: none;
  }
  .brand__name {
    font-size: 30px;
    letter-spacing: 0.5px;
  }
  .card--front .brand {
    left: 448px;
    top: 240px;
    color: var(--accent-navy);
  }
  .card--back .brand {
    left: 50%;
    top: 50%;
    transform: translate(-50%, -50%);
    color: var(--light-type);
  }
  .card--back .brand__name {
    font-size: 36px;
  }
  .card--back .brand__mark {
    width: 48px;
    height: 48px;
  }

  .colour-bands {
    position: absolute;
    left: 0;
    bottom: 0;
    width: 748px;
    height: 22px;
    display: flex;
    gap: 3px;
  }
  .colour-bands span {
    flex: 1;
  }
  .colour-bands .band--red { background: var(--accent-red); }
  .colour-bands .band--yellow { background: var(--accent-yellow); }
  .colour-bands .band--navy { background: var(--accent-navy); }
</style>
</head>
<body>
  <section class="card card--front" aria-label="Business card front">
    <div class="contact">
      <p class="contact__name">Daniel Hargrove</p>
      <p class="contact__role">CEO/Founder</p>
      <address class="contact__address">4120 Juniper Court<br>Fairbanks<br>Alaska 99701</address>
      <ul class="contact__lines">
        <li><span class="contact__label">P :</span> 907 555 0142</li>
        <li><span class="contact__label">F :</span> 907 555 0187</li>
        <li><span class="contact__label">M :</span> 907 555 0163</li>
        <li>hello@velorafilm.com</li>
        <li>www.velorafilm.com</li>
      </ul>
    </div>
    <div class="brand">
      <span class="brand__mark"></span>
      <span class="brand__name">Velora<br>Entertainment</span>
    </div>
    <div class="colour-bands">
      <span class="band--red"></span>
      <span class="band--yellow"></span>
      <span class="band--navy"></span>
    </div>
  </section>

  <section class="card card--back" aria-label="Business card back">
    <div class="brand">
      <span class="brand__mark"></span>
      <span class="brand__name">Velora<br>Entertainment</span>
    </div>
  </section>
</body>
</html>
```